Executive recruiting firm in need of business card design

Executive recruiting firm looking for a sleek, classy and modern business card design; card itself will be square shape, rounded edges and soft touch paper, our colors are dark blues in the navy color scale, silvers and grays. Reference our website for a better idea of our company's feel and goals at Tarvex-Up.com - our company message is "Employee Engagement Begins at Recruitment" this should be on the card

```html
<!DOCTYPE html>
<html lang="en">
<head>
<meta charset="utf-8">
<title>Tarvex-Up Business Card</title>
<link href="https://fonts.googleapis.com/css2?family=Open+Sans:wght@400;600;700&display=swap" rel="stylesheet">
<style>
  :root {
    --backdrop: #dedede;
    --navy: #161746;
    --white: #ffffff;
    --font: "Open Sans", Arial, sans-serif;
  }
  * { margin: 0; padding: 0; box-sizing: border-box; }
  html, body {
    width: 1200px;
    height: 900px;
    overflow: hidden;
    background: var(--backdrop);
    font-family: var(--font);
  }
  .canvas {
    position: relative;
    width: 1200px;
    height: 900px;
  }
  .card {
    position: absolute;
    top: 275px;
    width: 477px;
    height: 294px;
    background: var(--navy);
    color: var(--white);
  }
  .card--front {
    left: 116px;
    border-radius: 0 78px 0 78px;
  }
  .card--back {
    left: 622px;
    border-radius: 78px 0 78px 0;
  }
  .holder {
    position: absolute;
    left: 22px;
    top: 34px;
  }
  .holder__name {
    font-size: 18px;
    font-weight: 600;
    line-height: 1.2;
  }
  .holder__title {
    font-size: 13px;
    font-weight: 400;
    line-height: 1.2;
  }
  .address {
    position: absolute;
    left: 22px;
    top: 94px;
    font-size: 13px;
    line-height: 15px;
  }
  .contacts {
    position: absolute;
    right: 24px;
    top: 66px;
    list-style: none;
    text-align: right;
    font-size: 13px;
    line-height: 20px;
  }
  .contacts li {
    display: flex;
    justify-content: flex-end;
    align-items: center;
    gap: 4px;
  }
  .contacts svg {
    width: 10px;
    height: 10px;
    flex: none;
  }
  .brand {
    position: absolute;
    font-size: 26px;
    font-weight: 600;
    letter-spacing: 0;
    color: var(--white);
    white-space: nowrap;
    line-height: 1;
  }
  .card--front .brand {
    left: 112px;
    top: 190px;
  }
  .card--back .brand {
    left: 0;
    right: 0;
    top: 126px;
    text-align: center;
  }
  .message {
    position: absolute;
    left: 0;
    right: 0;
    top: 238px;
    text-align: center;
    font-size: 13px;
    font-weight: 600;
  }
</style>
</head>
<body>
<main class="canvas">

  <section class="card card--front" aria-label="Business card front">
    <div class="holder">
      <p class="holder__name">Daniel Morrow</p>
      <p class="holder__title">Managing Director</p>
    </div>
    <p class="address">12345, Address Goes Here<br>Country Name, 123456</p>
    <ul class="contacts">
      <li>(044)-318-2265
        <svg viewBox="0 0 10 10" aria-hidden="true"><path fill="#fff" d="M2.2 0.6 3.6 2.6 2.7 3.6C3.3 4.9 4.9 6.5 6.3 7.2L7.3 6.3 9.4 7.7 8.6 9.3C4.5 9.4 0.6 5.5 0.7 1.4Z"/></svg>
      </li>
      <li>info@tarvex-up.com
        <svg viewBox="0 0 10 10" aria-hidden="true"><rect x="0.5" y="2" width="9" height="6.5" fill="#fff"/><path d="M0.8 2.3 5 5.6 9.2 2.3" stroke="#161746" stroke-width="0.9" fill="none"/></svg>
      </li>
      <li>www.Tarvex-Up.com
        <svg viewBox="0 0 10 10" aria-hidden="true"><circle cx="5" cy="5" r="4.6" fill="#fff"/><path d="M0.6 5H9.4M5 0.4C2.8 3 2.8 7 5 9.6M5 0.4C7.2 3 7.2 7 5 9.6" stroke="#161746" stroke-width="0.7" fill="none"/></svg>
      </li>
    </ul>
    <p class="brand">Tarvex-Up</p>
  </section>

  <section class="card card--back" aria-label="Business card back">
    <p class="brand">Tarvex-Up</p>
    <p class="message">Employee Engagement Begins at Recruitment</p>
  </section>

</main>
</body>
</html>
```